Vantro cards

I am in the auto motive, transportation business I would like a business card that is Something cool, modern edgy, having to do with car culture. I offer towing service for high and exotic cars. I also provide towing for collisions and car accidents. I offer open and enclosed transport nationwide.

Target Market(s)

Car culture people high end auto collectors

Industry/Entity Type

Towing car carrier

Contact Information for Business Card

My company colors black yellow and silver

Font styles to use
Serif

```html
<!DOCTYPE html>
<html lang="en">
<head>
<meta charset="utf-8">
<title>Vantro Business Cards</title>
<link href="https://fonts.googleapis.com/css2?family=Arvo:wght@400;700&display=swap" rel="stylesheet">
<style>
  :root {
    --bg: #2b2b2b;
    --card-yellow: #fbdf5f;
    --emboss-gold: #d8b93a;
    --ink: #111111;
    --paper-white: #ffffff;
  }
  * { margin: 0; padding: 0; box-sizing: border-box; }
  html, body { width: 1200px; height: 1015px; overflow: hidden; }
  body {
    background: var(--bg);
    font-family: "Arvo", serif;
    color: var(--ink);
    position: relative;
  }
  .card {
    position: absolute;
    left: 290px;
    width: 620px;
    height: 354px;
    overflow: hidden;
    background: var(--card-yellow);
    box-shadow: 0 12px 30px rgba(0,0,0,.5);
  }
  .card--back { top: 110px; }
  .card--front { top: 548px; }

  .back-mark {
    position: absolute;
    inset: 0;
    display: flex;
    align-items: center;
    justify-content: center;
    gap: 18px;
  }
  .back-mark__dot {
    width: 34px; height: 34px;
    border-radius: 50%;
    background: var(--emboss-gold);
  }
  .back-mark__name {
    font-size: 64px;
    font-weight: 700;
    letter-spacing: 4px;
    color: var(--emboss-gold);
    text-transform: uppercase;
  }

  .front-circle { position: absolute; inset: 0; }
  .front-brand {
    position: absolute;
    left: 395px;
    top: 134px;
    width: 210px;
    text-align: center;
    font-size: 40px;
    line-height: 52px;
    font-weight: 700;
    letter-spacing: 2px;
    text-transform: uppercase;
    color: var(--ink);
  }
  .holder { position: absolute; left: 40px; top: 52px; }
  .holder__name { font-size: 23px; font-weight: 700; letter-spacing: 1px; text-transform: uppercase; }
  .holder__role { font-size: 15px; margin-top: 2px; }

  .contact { position: absolute; left: 118px; top: 196px; font-size: 15px; line-height: 20px; }
  .contact__address { margin-bottom: 14px; }
  .contact__line { display: flex; align-items: center; gap: 8px; }
  .contact__line svg { width: 15px; height: 15px; flex: none; }
</style>
</head>
<body>

<section class="card card--back" aria-label="Card back">
  <div class="back-mark">
    <span class="back-mark__dot"></span>
    <span class="back-mark__name">Vantro</span>
  </div>
</section>

<section class="card card--front" aria-label="Card front">
  <svg class="front-circle" viewBox="0 0 620 354" aria-hidden="true">
    <circle cx="545" cy="160" r="176" fill="var(--paper-white)"/>
    <path d="M448.6 22.4 A168 168 0 0 0 530.4 327.4" fill="none" stroke="var(--ink)" stroke-width="4"/>
    <circle cx="545" cy="160" r="163" fill="var(--paper-white)"/>
  </svg>

  <div class="front-brand">Vantro</div>

  <div class="holder">
    <div class="holder__name">Marcus Hale</div>
    <div class="holder__role">Managing Director</div>
  </div>

  <div class="contact">
    <div class="contact__address">421, Address line here<br>Country Name, 45452</div>
    <div class="contact__line">
      <svg viewBox="0 0 16 16"><path d="M3 1.5l3 .5 1 3-2 1.2a9 9 0 0 0 4.8 4.8L11 9l3 1 .5 3-2 2C6 14.5 1.5 10 1 3.5z" fill="var(--ink)"/></svg>
      <span>044-987 654 321</span>
    </div>
    <div class="contact__line">
      <svg viewBox="0 0 16 16"><rect x="1" y="3" width="14" height="10" fill="var(--ink)"/><path d="M1.5 3.5 8 9l6.5-5.5" fill="none" stroke="var(--card-yellow)" stroke-width="1.2"/></svg>
      <span>info@vantromail.com</span>
    </div>
    <div class="contact__line">
      <svg viewBox="0 0 16 16" fill="none" stroke="var(--ink)" stroke-width="1.4"><circle cx="8" cy="8" r="6.5"/><ellipse cx="8" cy="8" rx="3" ry="6.5"/><path d="M1.5 8h13M2.5 4.5h11M2.5 11.5h11"/></svg>
      <span>www.vantroline.com</span>
    </div>
  </div>
</section>

</body>
</html>
```